Sunset Harbor Living Web Page

We need a web page design that has two intro pages - first being a 'home page', then a link to the second page that has the 'content tabs' and a 'call to action' (see below).

The business helps people that wish to retire to S.E.Asia (Thailand, Malaysia, Indonesia,The Philippines etc) - to enjoy the lifestyle and the remaining years of their lives. What attracts S.E.Asia to many people is the lower cost, the atmoshpere and beauty of the tropics and the vibrancy of the various countries.

People that are wishing to make the most of their retirement and are adventurous at a great bargain compared to the cost of their own countries will be interested.

We help them achieve this - visa, financials (tax, gov't payments etc), introduce them to the right people for property, clubs, retirement facilities, insurance and so forth.

Therefore we are providing an extremely wide ranging service and this site will provide broad but general information only - with a call to action to come and see us for more specific information and how we can help them specifically.

This site will be predominantly for travel and lifestyle, it will be linked with another financial services (financial planning) site later down the track.

The colour scheme is dark green and blue - as per the attached logo design. Photos and background just think lifestyle and S.E.Asia - beaches/mountains/water/recreational activities for retirees.

Target market is mostly those coming up to retirement to those that are already retired. But we also expect to have some interest with younger people that would like to find out more and plan for the future. So a broad age group but I would say mostly 40-70 yrs old.

On the first (Home) page we would like our company name 'Sunset Harbor Living', our logo (which will be on all pages) and a statement such as: “Imagine a retirement where your dreams are brought to life, and you have never felt more alive. Let us show you how”. Then a link to the second page.

We would like an uncluttered site. On the second (contents) page the tabs would be:

- Visa
- Property
- Financials
- Travel
- Insurance & Healthcare
- Medical Tourism
- Cost of living
- Weekly Blogs and articles
- Sunset Harbor Living story

We would also like a call to action on the second page - asking them to leave their contact details if they wish to learn more or sign up to our weekly newsletter/blog.

We are open to suggestions and your imaginations.

Thank you
Malcolm

Font styles to use
Serif
Script

Colors
0255a3
3377b5
00a990
9bcb3c
abd036
33b8a4
85abd2
cadf82
86cfc6

Requirements
Must have
• I have been asked by the web designer to receive a 'Web Font' so that we can 'get off of Zentrofy'. Hope that makes sense.

```html
<!DOCTYPE html>
<html lang="en">
<head>
<meta charset="utf-8">
<title>Sunset Harbor Living</title>
<link rel="stylesheet" href="https://fonts.googleapis.com/css2?family=Lato:wght@300;400;700&family=Roboto:wght@400;500&display=swap">
<style>
:root{
  --green:#1cbb55;
  --green-dark:#14a548;
  --blue:#1597d3;
  --band:#1e9ad8;
  --ink:#1d1d1d;
  --text:#6b6b6b;
  --muted:#8a8a8a;
  --gray-bg:#efeff1;
  --footer:#1f1f20;
  --white:#ffffff;
}
*{box-sizing:border-box;margin:0;padding:0}
html,body{width:1200px;height:2372px;overflow:hidden}
body{position:relative;background:var(--white);font-family:'Lato',sans-serif;color:var(--ink)}
.abs{position:absolute}

/* header */
.brand{left:76px;top:30px;display:flex;align-items:center;gap:10px}
.brand-dot{width:40px;height:40px;border-radius:50%;background:var(--green)}
.brand-name{font-weight:700;font-size:21px;color:var(--blue);line-height:1}
.top-links{right:76px;top:28px;font-family:'Roboto',sans-serif;font-size:12px;color:var(--muted);letter-spacing:.3px}
.top-links span{margin:0 9px}
.call{right:76px;top:64px;font-family:'Roboto',sans-serif;font-size:12px;color:#555}
.call b{font-size:19px;font-weight:500;color:#111;margin-left:4px}

/* nav */
.main-nav{left:0;top:119px;width:1200px;height:47px;background:linear-gradient(var(--green),var(--green-dark));display:flex;padding-left:70px}
.main-nav a{font-family:'Roboto',sans-serif;font-size:12px;color:var(--white);text-decoration:none;padding:0 18px;line-height:47px;border-right:1px solid rgba(255,255,255,.25);text-transform:uppercase}
.main-nav a:last-child{border-right:0}

/* hero */
.hero{left:0;top:166px;width:1200px;height:574px;background:linear-gradient(180deg,#e9ebec 0%,#b7bcbf 22%,#6b7075 45%,#3a3d40 70%,#202224 100%)}
.hero-title{left:76px;top:350px;font-size:43px;font-weight:400;color:var(--white);line-height:53px}
.dots{left:553px;top:549px;display:flex;gap:6px;align-items:center}
.dots i{width:10px;height:10px;border-radius:50%;background:var(--white)}
.dots i.on{width:15px;height:15px;background:none;border:2px solid var(--white)}
.feature{top:620px;display:flex;gap:22px}
.feature .ring{width:92px;height:92px;border:3px solid var(--white);border-radius:50%;display:flex;align-items:center;justify-content:center;color:var(--white);font-size:40px;flex:none}
.feature h3{font-weight:400;font-size:19px;color:var(--white);margin-top:4px}
.feature p{font-size:12px;color:#ccc;line-height:17px;margin-top:6px;width:190px}

/* welcome */
.section-title{font-size:28px;font-weight:400;color:var(--ink)}
.section-title em{font-style:normal;color:var(--blue)}
.welcome-title{left:0;width:1200px;top:808px;text-align:center}
.welcome-text{left:104px;width:998px;top:862px;text-align:center;font-size:13px;line-height:22px;color:var(--text)}
.card{top:955px;width:254px}
.card .photo{height:201px}
.card p{text-align:center;font-size:15px;letter-spacing:.6px;color:#333;margin-top:20px;text-transform:uppercase}
.arrow{top:1037px;width:32px;height:32px;background:#222;display:flex;align-items:center;justify-content:center}

/* weekly */
.weekly{left:0;top:1243px;width:1200px;height:453px;background:var(--gray-bg)}
.article{display:flex;gap:27px}
.article .thumb{width:114px;height:103px;border:3px solid var(--white);box-shadow:0 0 0 1px #ddd;flex:none}
.article h4{font-weight:400;font-size:17px;color:var(--ink);margin-top:-2px}
.article .meta{font-size:11.5px;color:var(--blue);margin-top:4px}
.article p{font-size:12px;line-height:17px;color:var(--muted);margin-top:10px;width:170px}
.blog-card{left:794px;width:332px;background:var(--white);padding:14px 20px;border:1px solid #e2e2e2}
.blog-card .date{font-size:12px;color:var(--blue)}
.blog-card p{font-size:12px;line-height:17px;color:var(--muted);margin-top:8px}

/* story */
.story{left:76px;top:1747px;width:1050px;height:293px;border:2px solid #e3e3e3}
.story-photo{left:104px;top:1783px;width:354px;height:222px;border:5px solid var(--white);box-shadow:0 0 0 1px #e4e4e4}
.story-title{left:495px;top:1786px;font-size:27px}
.story-text{left:495px;top:1834px;width:598px;font-size:13px;line-height:22px;color:var(--text)}
.btn-more{left:498px;top:1945px;width:142px;height:39px;background:var(--blue);color:var(--white);font-size:12px;display:flex;align-items:center;justify-content:center;letter-spacing:.5px}

/* newsletter */
.newsletter{left:0;top:2095px;width:1200px;height:108px;background:var(--band)}
.nl-title{left:166px;top:2138px;display:flex;align-items:center;gap:18px;color:var(--white);font-size:27px}
.nl-input{left:487px;top:2133px;width:387px;height:41px;background:var(--white);font-size:12px;color:#888;padding-left:18px;line-height:41px}
.nl-btn{left:888px;top:2133px;width:152px;height:41px;background:#222;color:var(--white);font-size:13px;display:flex;align-items:center;justify-content:center;letter-spacing:.5px}

/* footer */
.site-footer{left:0;top:2203px;width:1200px;height:169px;background:var(--footer)}
.social{left:76px;top:2250px;display:flex;gap:9px}
.social i{width:28px;height:28px;border-radius:50%;background:#d8d8d8}
.footer-links{left:76px;top:2295px;font-size:13px;color:#aaa}
.footer-links span{margin:0 10px}
.copyright{left:76px;top:2318px;font-size:13px;color:#aaa}
.footer-brand{left:1000px;top:2296px;display:flex;align-items:center;gap:8px}
.footer-brand .brand-dot{width:26px;height:26px;background:#555}
.footer-brand span{font-weight:700;font-size:14px;color:#777}
</style>
</head>
<body>

<header>
  <div class="abs brand"><span class="brand-dot"></span><span class="brand-name">Sunset Harbor Living</span></div>
  <div class="abs top-links">HOME<span>|</span>WEEKLY BLOGS AND ARTICLES<span>|</span>CONTACT US</div>
  <div class="abs call">GIVE US A CALL: <b>(555) 018 2046</b></div>
</header>

<nav class="abs main-nav">
  <a>Visa</a><a>Property</a><a>Financials</a><a>Travel</a><a>Insurance &amp; Healthcare</a><a>Medical Tourism</a><a>Cost of Living</a><a>Sunset Harbor Living Story</a><a>Contact Us</a>
</nav>

<section>
  <div class="abs hero" role="img" aria-label="Snow-capped mountain range under a pale sky"></div>
  <h1 class="abs hero-title">Enjoy the lifestyle &amp; the<br>remaining years of your lives</h1>
  <div class="abs dots"><i></i><i></i><i class="on"></i><i></i><i></i><i></i></div>

  <div class="abs feature" style="left:76px">
    <div class="ring"><svg width="42" height="46" viewBox="0 0 42 46" fill="none" stroke="#fff" stroke-width="3.5" stroke-linecap="round"><circle cx="21" cy="7" r="4"/><line x1="21" y1="11" x2="21" y2="42"/><line x1="12" y1="18" x2="30" y2="18"/><path d="M4 28c2 9 9 14 17 14s15-5 17-14"/></svg></div>
    <div><h3>ENJOY LIFESTYLE</h3><p>Neque porro quisquam est, qui dolorem ipsum quia dolor sit um amet, consectetur</p></div>
  </div>
  <div class="abs feature" style="left:452px">
    <div class="ring" style="font-weight:700">$</div>
    <div><h3>LOWER COST</h3><p>Neque porro quisquam est, qui dolorem ipsum quia dolor sit um amet, consectetur</p></div>
  </div>
  <div class="abs feature" style="left:827px">
    <div class="ring"><svg width="40" height="40" viewBox="0 0 40 40" fill="none" stroke="#fff" stroke-width="3" stroke-linejoin="round"><path d="M36 4 4 18l12 5 4 13 16-32z"/><path d="M16 23 36 4"/></svg></div>
    <div><h3>LEARN ABOUT US</h3><p>Neque porro quisquam est, qui dolorem ipsum quia dolor sit um amet, consectetur</p></div>
  </div>
</section>

<section>
  <h2 class="abs section-title welcome-title">Welcome to <em>Sunset Harbor Living</em></h2>
  <p class="abs welcome-text">Lorem ipsum dolor sit amet, consectetur adipiscing elit, sed do eiusmod tempor incididunt ut labore et dolore magna aliqua. Ut enim ad minim veniam, quis nostrud exercitation ullamco laboris nisi ut aliquip ex ea commodo consequat. Duis aute irure dolor in reprehenderit in voluptate velit esse cillum dolore eu fugiat nulla pariatur. Excepteur sint occaecat cupidatat non proident, sunt in culpa qui officia deserunt mollit anim id est laborum.</p>

  <div class="abs card" style="left:65px"><div class="photo" role="img" aria-label="Retired couple walking on a sunny beach" style="background:linear-gradient(#dfe7ee,#e8dcc6)"></div><p>Health Care</p></div>
  <div class="abs card" style="left:337px"><div class="photo" role="img" aria-label="Nurse caring for an elderly woman" style="background:linear-gradient(#d9d3cc,#b8a59a)"></div><p>Medical Tourism</p></div>
  <div class="abs card" style="left:609px"><div class="photo" role="img" aria-label="Coins resting on a printed statement" style="background:linear-gradient(#ecebe6,#b89a5e)"></div><p>Cost of Living</p></div>
  <div class="abs card" style="left:882px"><div class="photo" role="img" aria-label="Smiling retired couple by the sea" style="background:linear-gradient(#9fd0ea,#e5dccd)"></div><p>Enjoy Traveling</p></div>

  <div class="abs arrow" style="left:76px"><svg width="12" height="14" viewBox="0 0 12 14"><path d="M9 1 3 7l6 6" fill="none" stroke="#fff" stroke-width="2.5"/></svg></div>
  <div class="abs arrow" style="left:1089px"><svg width="12" height="14" viewBox="0 0 12 14"><path d="M3 1l6 6-6 6" fill="none" stroke="#fff" stroke-width="2.5"/></svg></div>
</section>

<section>
  <div class="abs weekly"></div>
  <h2 class="abs section-title" style="left:76px;top:1296px">Weekly <em>Articles</em></h2>
  <h2 class="abs section-title" style="left:795px;top:1296px">Weekly <em>Blog</em></h2>

  <div class="abs article" style="left:76px;top:1360px"><div class="thumb" role="img" aria-label="Grandfather walking with grandson" style="background:linear-gradient(#e6e6e6,#b7b0a4)"></div><div><h4>Finibus Bonorum et</h4><div class="meta">posted by 05 apr 2016</div><p>Duis aute irure dolor in reprh enderit in voluptate velit esse cillum dolore eu fugiat</p></div></div>
  <div class="abs article" style="left:451px;top:1360px"><div class="thumb" role="img" aria-label="Elderly couple holding hands outdoors" style="background:linear-gradient(#6f9a4e,#3f6a2c)"></div><div><h4>Voluptatem Accusa</h4><div class="meta">posted by 05 apr 2016</div><p>Duis aute irure dolor in reprh enderit in voluptate velit esse cillum dolore eu fugiat</p></div></div>
  <div class="abs article" style="left:76px;top:1524px"><div class="thumb" role="img" aria-label="Portrait of a smiling senior woman" style="background:linear-gradient(#d8d2c6,#9a8a78)"></div><div><h4>Totam Rem Aper</h4><div class="meta">posted by 05 apr 2016</div><p>Duis aute irure dolor in reprh enderit in voluptate velit esse cillum dolore eu fugiat</p></div></div>
  <div class="abs article" style="left:451px;top:1524px"><div class="thumb" role="img" aria-label="Senior couple jogging in a park" style="background:linear-gradient(#efe2c0,#b9a67a)"></div><div><h4>Nemo Enim Ips</h4><div class="meta">posted by 05 apr 2016</div><p>Duis aute irure dolor in reprh enderit in voluptate velit esse cillum dolore eu fugiat</p></div></div>

  <div class="abs blog-card" style="top:1356px"><div class="date">05 apr 2016</div><p>Duis aute irure dolor in reprh enderit in voluptate velit esse cillum dolore eu fugiat</p></div>
  <div class="abs blog-card" style="top:1453px"><div class="date">05 apr 2016</div><p>Ut enim ad minim veniam, quis nostrud exercitation ullamco laboris nisi ut aliquip.</p></div>
  <div class="abs blog-card" style="top:1549px"><div class="date">05 apr 2016</div><p>Duis aute irure dolor in reprh enderit in voluptate velit esse cillum dolore eu fugiat</p></div>
</section>

<section>
  <div class="abs story"></div>
  <div class="abs story-photo" role="img" aria-label="Happy retired couple on the beach" style="background:linear-gradient(#cfe2ee,#e7ddcd)"></div>
  <h2 class="abs section-title story-title">Sunset Harbor <em>Living Story</em></h2>
  <p class="abs story-text">Lorem ipsum dolor sit amet, consectetur adipiscing elit, sed do eiusmod tempor incididunt ut labore et dolore magna aliqua. Ut enim ad minim veniam, quis nostrud exercitation ullamco laboris nisi ut aliquip ex ea commodo consequat. Duis aute irure dolor in reprehenderit in voluptate velit esse cillum dolore eu fugiat nulla pariatur. Excepteur sint occaecat cupidatat non.</p>
  <div class="abs btn-more">READ MORE</div>
</section>

<section>
  <div class="abs newsletter"></div>
  <div class="abs nl-title"><svg width="36" height="27" viewBox="0 0 36 27" fill="none" stroke="#fff" stroke-width="2.5"><rect x="2" y="2" width="32" height="23" rx="2"/><path d="M2 4l16 12L34 4"/></svg>Weekly Newsletter</div>
  <div class="abs nl-input">Enter your Email Address</div>
  <div class="abs nl-btn">SUBSCRIBE</div>
</section>

<footer>
  <div class="abs site-footer"></div>
  <div class="abs social"><i></i><i></i><i></i><i></i></div>
  <div class="abs footer-links">Home<span>/</span>About Us<span>/</span>Services<span>/</span>Privacy Policy<span>/</span>Terms of Use<span>/</span>Contact Us</div>
  <div class="abs copyright">Copyright (c) 2016, All Right Reserved.</div>
  <div class="abs footer-brand"><span class="brand-dot"></span><span>Sunset Harbor Living</span></div>
</footer>

</body>
</html>
```